BRIGHT RIVER POWER.

I'd like my business logo.
contact name: Dennis Halvorsen
phone:0438759164
email: info@brightriverpower.net.au
website: www.brightriverpower.net.au

services:
solar
battery storage
LED lighting
energy saving solutions
general electrical
I'd like the design to look professional

Target Market(s)

Everyone

Industry/Entity Type

Business

Contact Information for Business Card

as described above

Requirements
Must have
• Id like the colours and the design to work well with my logo.

```html
<!DOCTYPE html>
<html lang="en">
<head>
<meta charset="utf-8">
<title>Bright River Power – Business Card</title>
<link href="https://fonts.googleapis.com/css2?family=Open+Sans:wght@400;600;700&display=swap" rel="stylesheet">
<style>
  :root {
    --backdrop-top: #262626;
    --backdrop-bottom: #0a0a0a;
    --card-white: #ffffff;
    --brand-orange: #f5a01a;
    --brand-green: #7cbc2a;
    --gradient-top: #9dcb32;
    --gradient-bottom: #4bb482;
    --text-light: #ffffff;
  }
  * { margin: 0; padding: 0; box-sizing: border-box; }
  html, body {
    width: 1200px;
    height: 900px;
    overflow: hidden;
  }
  body {
    position: relative;
    background: linear-gradient(180deg, var(--backdrop-top) 0%, var(--backdrop-bottom) 100%);
    font-family: "Open Sans", sans-serif;
  }
  .card {
    position: absolute;
    top: 306px;
    width: 440px;
    height: 271px;
    border-radius: 12px;
    box-shadow: 0 4px 14px rgba(0,0,0,0.45);
    overflow: hidden;
  }
  .card--front {
    left: 149px;
    background: var(--card-white);
  }
  .card--back {
    left: 608px;
    background: linear-gradient(180deg, var(--gradient-top) 0%, var(--gradient-bottom) 100%);
    color: var(--text-light);
    text-align: center;
  }
  .front-mark {
    position: absolute;
    left: 56px;
    top: 96px;
    width: 130px;
    display: flex;
    flex-direction: column;
    align-items: center;
    gap: 8px;
  }
  .front-mark__dot {
    width: 40px;
    height: 40px;
    border-radius: 50%;
    background: var(--brand-orange);
  }
  .front-mark__name {
    font-size: 13px;
    font-weight: 700;
    color: var(--brand-green);
    letter-spacing: 0.5px;
    text-align: center;
    line-height: 1.2;
  }
  .contact {
    position: absolute;
    left: 208px;
    top: 92px;
  }
  .contact__name {
    font-size: 14.5px;
    font-weight: 600;
    color: var(--brand-orange);
    margin-bottom: 25px;
  }
  .contact__list { list-style: none; }
  .contact__item {
    display: flex;
    align-items: center;
    gap: 6px;
    font-size: 12.5px;
    line-height: 16px;
    color: var(--brand-green);
  }
  .contact__icon {
    width: 9px;
    height: 9px;
    flex: none;
    fill: var(--brand-orange);
  }
  .back-brand {
    margin-top: 78px;
    font-size: 30px;
    font-weight: 700;
    letter-spacing: 1px;
    line-height: 1.1;
  }
  .services__title {
    margin-top: 44px;
    font-size: 13.5px;
    font-weight: 600;
  }
  .services__list {
    margin-top: 12px;
    font-size: 12px;
    line-height: 16px;
  }
</style>
</head>
<body>
  <section class="card card--front" aria-label="Business card front">
    <div class="front-mark">
      <span class="front-mark__dot"></span>
      <span class="front-mark__name">BRIGHT RIVER POWER</span>
    </div>
    <div class="contact">
      <p class="contact__name">Dennis Halvorsen</p>
      <ul class="contact__list">
        <li class="contact__item">
          <svg class="contact__icon" viewBox="0 0 10 10" aria-hidden="true"><path d="M2 0.5 L3.6 0.5 L4.3 2.8 L3.2 3.6 Q4.2 5.8 6.4 6.8 L7.2 5.7 L9.5 6.4 L9.5 8 Q9.5 9.5 8 9.5 Q0.5 9 0.5 2 Q0.5 0.5 2 0.5Z"/></svg>
          0438759164
        </li>
        <li class="contact__item">
          <svg class="contact__icon" viewBox="0 0 10 10" aria-hidden="true"><path d="M0.5 2 H9.5 V8.5 H0.5Z M1 2.5 L5 5.5 L9 2.5" stroke="#fff" stroke-width="0.8"/></svg>
          info@brightriverpower.net.au
        </li>
        <li class="contact__item">
          <svg class="contact__icon" viewBox="0 0 10 10" aria-hidden="true"><circle cx="5" cy="5" r="4.5"/></svg>
          www.brightriverpower.net.au
        </li>
      </ul>
    </div>
  </section>

  <section class="card card--back" aria-label="Business card back">
    <p class="back-brand">BRIGHT RIVER POWER</p>
    <div class="services">
      <p class="services__title">WHAT I DO</p>
      <p class="services__list">Solar | Battery Storage<br>LED Lighting | Energy Saving Solutions</p>
    </div>
  </section>
</body>
</html>
```